Business card design Needed for new logo / Construction business, home extensions and new builds

We need a business card design using our new logo files which i will attach to this project :)

We are a small construction business specialising in home extensions, new builds and property development. We are very ambitious and would appreciate professional and elegant designs for our new business card.

Very serious about using the services on MakerQuarry and recently acquired our new logo from here :)

Please get involved, i will feedback when i can as i am very busy but can respond daily, thanks

Target Market(s)

People that want to build onto their houses, new building developments or adding too their existing property

Industry/Entity Type

Construction

Contact Information for Business Card

Renwick Tolliver Construction, Lionel Ashby (Managing Director), Tel 07822254961, email - info@renwick-tolliver, www.renwick-tolliver.co.uk

Colors

Designer to choose colors to be used in the design.

Requirements
Must have
• I like a deep grey on the back please. A lot of you have provided black from and back, try mixing things up a little. The black looks cool 😎 Thanks

```html
<!DOCTYPE html>
<html lang="en">
<head>
<meta charset="utf-8">
<title>Renwick Tolliver Construction – Business Card</title>
<link rel="stylesheet" href="https://fonts.googleapis.com/css2?family=Cinzel:wght@500;600&family=Montserrat:wght@400;500&display=swap">
<style>
  :root {
    --stage: #262626;
    --card-grey: #666666;
    --card-back: #5a5a5a;
    --pattern-light: #7a7a7a;
    --pattern-dark: #3e3e3e;
    --gold: #e0a73a;
    --gold-edge: #d49a2e;
    --silver: #d6d6d6;
    --white: #f4f4f4;
    --rule: #8a8a8a;
  }
  * { box-sizing: border-box; margin: 0; padding: 0; }
  html, body { width: 1200px; height: 987px; overflow: hidden; }
  body {
    background: var(--stage);
    position: relative;
    font-family: "Montserrat", sans-serif;
  }
  .card {
    position: absolute;
    left: 250px;
    width: 700px;
    height: 410px;
    border-radius: 22px;
    border: 3px solid var(--gold-edge);
    overflow: hidden;
  }
  .card--back { top: 50px; background: var(--card-back); }
  .card--front { top: 527px; background: var(--card-grey); }

  .back-pattern {
    position: absolute; inset: 0;
    background: linear-gradient(135deg, var(--pattern-dark) 0%, var(--card-back) 50%, var(--pattern-light) 100%);
  }
  .back-mark {
    position: absolute; right: 70px; top: 182px;
    display: flex; align-items: center; gap: 8px;
  }
  .back-mark__square { width: 10px; height: 10px; background: var(--gold); }
  .back-mark__name {
    font-family: "Cinzel", serif; font-weight: 600; font-size: 15px;
    letter-spacing: 1px; color: var(--gold);
  }

  .brand {
    position: absolute; left: 0; right: 0; top: 70px;
    text-align: center;
  }
  .brand__square { width: 16px; height: 16px; background: var(--gold); margin: 0 auto 18px; }
  .brand__name {
    font-family: "Cinzel", serif; font-weight: 500; color: var(--silver);
    font-size: 34px; letter-spacing: 2px; line-height: 1.1;
  }
  .brand__sub {
    font-family: "Cinzel", serif; font-weight: 500; color: var(--silver);
    font-size: 18px; letter-spacing: 5px; margin-top: 4px;
  }

  .person {
    position: absolute; left: 60px; top: 280px; width: 250px; text-align: right;
  }
  .person__name {
    font-family: "Cinzel", serif; font-weight: 600; color: var(--gold);
    font-size: 26px; letter-spacing: 1px;
  }
  .person__role { color: var(--white); font-size: 17px; margin-top: 2px; }

  .divider {
    position: absolute; left: 335px; top: 260px; width: 1px; height: 100px;
    background: var(--rule);
  }

  .contact {
    position: absolute; left: 360px; top: 262px; list-style: none;
  }
  .contact__item {
    display: flex; align-items: center; gap: 10px;
    color: var(--white); font-size: 17px; line-height: 32px;
  }
  .contact__icon { width: 14px; height: 14px; flex: none; }
</style>
</head>
<body>

  <section class="card card--back" aria-label="Card back">
    <div class="back-pattern" role="img" aria-label="Repeating embossed company monogram pattern in light and dark grey"></div>
    <div class="back-mark">
      <span class="back-mark__square"></span>
      <span class="back-mark__name">Renwick Tolliver</span>
    </div>
  </section>

  <section class="card card--front" aria-label="Card front">
    <div class="brand">
      <div class="brand__square"></div>
      <div class="brand__name">RENWICK TOLLIVER</div>
      <div class="brand__sub">CONSTRUCTION</div>
    </div>

    <div class="person">
      <div class="person__name">LIONEL ASHBY</div>
      <div class="person__role">Managing Director</div>
    </div>

    <div class="divider"></div>

    <ul class="contact">
      <li class="contact__item">
        <svg class="contact__icon" viewBox="0 0 24 24" aria-hidden="true"><path fill="#e0a73a" d="M6.6 10.8a15 15 0 0 0 6.6 6.6l2.2-2.2c.3-.3.7-.4 1-.2 1.1.4 2.3.6 3.6.6.6 0 1 .4 1 1V20c0 .6-.4 1-1 1A17 17 0 0 1 3 4c0-.6.4-1 1-1h3.5c.6 0 1 .4 1 1 0 1.3.2 2.5.6 3.6.1.3 0 .7-.2 1z"/></svg>
        07822254961
      </li>
      <li class="contact__item">
        <svg class="contact__icon" viewBox="0 0 24 24" aria-hidden="true"><path fill="#e0a73a" d="M2 5h20v14H2zm2 2v.5l8 5 8-5V7z"/></svg>
        info@renwick-tolliver
      </li>
      <li class="contact__item">
        <svg class="contact__icon" viewBox="0 0 24 24" aria-hidden="true"><circle cx="12" cy="12" r="9" fill="none" stroke="#e0a73a" stroke-width="2.5"/><path d="M3 12h18M12 3c3 3 3 15 0 18M12 3c-3 3-3 15 0 18" fill="none" stroke="#e0a73a" stroke-width="1.8"/></svg>
        www.renwick-tolliver.co.uk
      </li>
    </ul>
  </section>

</body>
</html>
```